Kelp Row Arc need a business card designed

Descriptions:

Kelp Row Arc is a recruiting firm that only recruits sales people. Our advantage In the market is that we use A.I. software to recruit and pre assess candidates to find the top 20% of talent.

Here is the copy needed on each side of the card

Side #1.

Photo/Headshot
THOMAS MERROW
CEO
555-318-4427
www.KelpRowArc.example
tmerrow@KelpRowArc.example
Fernhollow, OR

"Finding & Hiring Sales People Sucks!"
"Using the power of A.I. assessment tools to find you the top 20% of sales talent guaranteed!"

Side 2.

"The True cost of a bad hire can be as high as 10 X the first year salary"

"With KELP ROW ARC:
50% Faster time to hire
83% New Hire retention
96% Of wrong hires eliminated
50% Lower sales turnover

Link to ZIP guidelines / Templates for PhotoShop, InDesgin & Illustrator:
https://www.filevaultly.example/scl/fo/qpzt7yrnwke2lsa4cdjbv/h?rlkey=tnw83kfpqzr1c5vyxlbe2ad9&dl=0

```html
<!DOCTYPE html>
<html lang="en">
<head>
<meta charset="utf-8">
<title>Kelp Row Arc – Business Card</title>
<link href="https://fonts.googleapis.com/css2?family=Montserrat:wght@400;500;600;700;800&display=swap" rel="stylesheet">
<style>
  :root {
    --navy: #0b3283;
    --sky: #0d9be0;
    --white: #ffffff;
    --ink: #1c1f2a;
    --stage: #d9d9d9;
  }
  * { box-sizing: border-box; margin: 0; padding: 0; }
  html, body { width: 1200px; height: 856px; overflow: hidden; }
  body {
    background: var(--stage);
    font-family: "Montserrat", sans-serif;
    display: flex; flex-direction: column; align-items: center; justify-content: center;
    gap: 36px;
  }
  .card {
    position: relative; width: 660px; height: 377px; overflow: hidden;
    box-shadow: 0 8px 24px rgba(0,0,0,.22);
  }

  /* ---------- front ---------- */
  .card--front { background: var(--white); color: var(--ink); }
  .brand { position: absolute; left: 28px; top: 38px; }
  .brand__row { display: flex; align-items: center; gap: 7px; }
  .brand__name { font-size: 22px; font-weight: 600; color: var(--navy); letter-spacing: 1px; line-height: 1; }
  .brand__dot { width: 10px; height: 10px; background: var(--sky); }
  .brand__tag { font-size: 7px; font-weight: 700; color: var(--navy); letter-spacing: 1.5px; margin-top: 5px; }

  .pitch {
    position: absolute; left: 300px; top: 30px; width: 320px;
    text-align: center; font-size: 13px; font-weight: 500; line-height: 1.5;
  }
  .band-navy { position: absolute; left: 0; top: 150px; width: 520px; height: 82px; background: var(--navy); }
  .band-sky { position: absolute; left: 520px; top: 112px; width: 140px; height: 34px; background: var(--sky); }
  .person { position: absolute; left: 40px; top: 162px; color: var(--white); }
  .person__name { font-size: 28px; font-weight: 800; letter-spacing: .5px; }
  .person__role { font-size: 17px; font-weight: 500; margin-top: 2px; }

  .portrait {
    position: absolute; left: 450px; top: 100px; width: 140px; height: 140px; border-radius: 50%;
    border: 3px solid var(--sky);
    background: radial-gradient(circle at 45% 40%, #6b6f78 0%, #3a3d45 55%, #1d2030 100%);
  }
  .contacts { position: absolute; left: 40px; top: 254px; list-style: none; }
  .contacts li { display: flex; align-items: center; gap: 12px; font-size: 15px; font-weight: 500; margin-bottom: 9px; }
  .contacts svg { width: 18px; height: 18px; flex: none; }
  .city { position: absolute; left: 460px; top: 278px; font-size: 15px; font-weight: 500; }
  .edge-navy { position: absolute; left: 0; bottom: 0; width: 468px; height: 12px; background: var(--navy); }
  .edge-sky { position: absolute; left: 472px; bottom: 0; width: 188px; height: 12px; background: var(--sky); }

  /* ---------- back ---------- */
  .card--back { background: var(--navy); color: var(--white); text-align: center; padding-top: 70px; }
  .mark { display: inline-block; text-align: right; }
  .mark__row { display: flex; align-items: center; gap: 12px; }
  .mark__name { font-size: 56px; font-weight: 500; letter-spacing: 2px; line-height: 1; }
  .mark__dot { width: 22px; height: 22px; background: var(--white); }
  .mark__tag { font-size: 12px; font-weight: 700; letter-spacing: 3px; margin-top: 8px; margin-right: 34px; }
  .rule { height: 1.5px; background: var(--white); }
  .rule--top { width: 520px; margin: 14px auto 16px; }
  .claim { font-size: 15.5px; font-weight: 500; }
  .with { display: flex; align-items: center; justify-content: center; gap: 12px; margin: 12px 0 14px; font-size: 15.5px; font-weight: 500; }
  .with .rule { width: 150px; }
  .stats { list-style: none; display: flex; flex-wrap: wrap; justify-content: center; gap: 10px 18px; width: 580px; margin: 0 auto; }
  .stats li { display: flex; align-items: center; gap: 8px; font-size: 15.5px; font-weight: 500; }
  .stats svg { width: 17px; height: 17px; }
</style>
</head>
<body>

<section class="card card--front" aria-label="Business card front">
  <div class="brand">
    <div class="brand__row"><span class="brand__name">KELP ROW ARC</span><span class="brand__dot"></span></div>
    <div class="brand__tag">YOUR A.I. SALES RECRUITER</div>
  </div>
  <p class="pitch">Finding &amp; Hiring Sales People Sucks!<br>Using the power of A.I. assessment tools to find you the top 20% of sales talent guaranteed!</p>

  <div class="band-sky"></div>
  <div class="band-navy"></div>
  <div class="person">
    <div class="person__name">THOMAS MERROW</div>
    <div class="person__role">CEO</div>
  </div>
  <div class="portrait" role="img" aria-label="Headshot of the CEO"></div>

  <ul class="contacts">
    <li>
      <svg viewBox="0 0 24 24" aria-hidden="true"><path fill="#0b3283" d="M6.6 10.8a15.1 15.1 0 0 0 6.6 6.6l2.2-2.2a1 1 0 0 1 1-.25 11.4 11.4 0 0 0 3.6.57 1 1 0 0 1 1 1V20a1 1 0 0 1-1 1A17 17 0 0 1 3 4a1 1 0 0 1 1-1h3.5a1 1 0 0 1 1 1c0 1.25.2 2.45.57 3.57a1 1 0 0 1-.25 1z"/></svg>
      555-318-4427
    </li>
    <li>
      <svg viewBox="0 0 24 24" aria-hidden="true"><rect x="2" y="5" width="20" height="14" rx="1.5" fill="#0b3283"/><path d="M3 6l9 7 9-7" stroke="#fff" stroke-width="1.6" fill="none"/></svg>
      tmerrow@KelpRowArc.example
    </li>
    <li>
      <svg viewBox="0 0 24 24" aria-hidden="true"><circle cx="12" cy="12" r="10" fill="#0b3283"/><path d="M2 12h20M12 2c3 3 3 17 0 20M12 2c-3 3-3 17 0 20" stroke="#fff" stroke-width="1.3" fill="none"/></svg>
      www.KelpRowArc.example
    </li>
  </ul>
  <div class="city">Fernhollow, OR</div>
  <div class="edge-navy"></div>
  <div class="edge-sky"></div>
</section>

<section class="card card--back" aria-label="Business card back">
  <div class="mark">
    <div class="mark__row"><span class="mark__name">KELP ROW ARC</span><span class="mark__dot"></span></div>
    <div class="mark__tag">YOUR A.I. SALES RECRUITER</div>
  </div>
  <div class="rule rule--top"></div>
  <p class="claim">The True cost of a bad hire can be as high as 10 X the first year salary</p>
  <div class="with"><span class="rule"></span>With KELP ROW ARC:<span class="rule"></span></div>
  <ul class="stats">
    <li><svg viewBox="0 0 24 24" aria-hidden="true"><circle cx="12" cy="12" r="10" stroke="#fff" stroke-width="2.2" fill="none"/><path d="M7 12l3.5 3.5L19 7" stroke="#fff" stroke-width="2.6" fill="none"/></svg>50% Faster time to hire</li>
    <li><svg viewBox="0 0 24 24" aria-hidden="true"><circle cx="12" cy="12" r="10" stroke="#fff" stroke-width="2.2" fill="none"/><path d="M7 12l3.5 3.5L19 7" stroke="#fff" stroke-width="2.6" fill="none"/></svg>83% New Hire retention</li>
    <li><svg viewBox="0 0 24 24" aria-hidden="true"><circle cx="12" cy="12" r="10" stroke="#fff" stroke-width="2.2" fill="none"/><path d="M7 12l3.5 3.5L19 7" stroke="#fff" stroke-width="2.6" fill="none"/></svg>96% Of wrong hires eliminated</li>
    <li><svg viewBox="0 0 24 24" aria-hidden="true"><circle cx="12" cy="12" r="10" stroke="#fff" stroke-width="2.2" fill="none"/><path d="M7 12l3.5 3.5L19 7" stroke="#fff" stroke-width="2.6" fill="none"/></svg>50% Lower sales turnover</li>
  </ul>
</section>

</body>
</html>
```